New manufacturing IT architecture concept powerpoint presentation

Create an appealing PowerPoint presentation, from handmade sketches, to illustrate a new approach to manufacturing IT architectures. We want to present the idea to augment the experience of people working in manufacturing plants using AI based on the data that our systems normally collect. We even want to present the power of having a tier 2 Manufacturing execution system that can coordinate and optimize production between multiple plants of the same corporate. The target audience is IT managers, Operations Managers, plant managers, engineering managers, and Continuous improvement managers.
Target Market(s)
Manufacturing companies mostly in Food & Bev and CPG. Mostly big multinational companies
Industry/Entity Type
Software manufacturing solutions (MES/MOM)
Font styles to use
Other font styles liked:
- Segoe
Look and feel

```html
<!DOCTYPE html>
<html lang="en">
<head>
<meta charset="utf-8">
<title>Unified Operation Center and Augmented Operation Management</title>
<link href="https://fonts.googleapis.com/css2?family=Poppins:wght@500;600;700;800&display=swap" rel="stylesheet">
<style>
  :root {
    --blue: #1b5aa8;
    --orange: #f0831f;
    --ink: #1d1d1f;
    --page-bg: #e4e5e7;
    --slide-bg: #ffffff;
    --grid: #dcdcdc;
    --muted: #4a4a4a;
  }
  * { margin: 0; padding: 0; box-sizing: border-box; }
  html, body { width: 1200px; height: 3886px; overflow: hidden; }
  body { background: var(--page-bg); font-family: "Poppins", "Segoe UI", sans-serif; position: relative; }
  .slide {
    position: absolute; left: 107px; width: 986px; height: 555px;
    background: var(--slide-bg); overflow: hidden;
    box-shadow: 0 1px 3px rgba(0,0,0,0.08);
  }
  .slide svg.full { position: absolute; left: 0; top: 0; width: 986px; height: 555px; }
  .footer-bar { position: absolute; bottom: 0; width: 9px; height: 32px; background: var(--blue); }
  .footer-bar.left { left: 0; }
  .footer-bar.right { right: 0; }
  .footer-label { position: absolute; left: 26px; bottom: 9px; font-size: 12px; font-weight: 700; color: var(--ink); }
  .page-no { position: absolute; right: 16px; bottom: 9px; font-size: 10px; font-weight: 500; color: var(--muted); }
  .marker { position: absolute; left: 0; top: 26px; width: 0; height: 0;
    border-top: 15px solid transparent; border-bottom: 15px solid transparent; border-left: 32px solid var(--orange); }
  .slide-title { position: absolute; left: 45px; top: 24px; font-size: 25px; font-weight: 700; color: var(--ink); letter-spacing: 0.2px; }
  .slide-sub { position: absolute; left: 47px; top: 70px; width: 880px; font-size: 14px; line-height: 26px; font-weight: 700; color: var(--ink); text-transform: uppercase; }

  .cover-photo { position: absolute; inset: 0;
    background: linear-gradient(135deg, #8f8a84 0%, #cfc7bb 35%, #e8e4de 55%, #6d6b6d 80%, #3c3b40 100%); }
  .cover-title { position: absolute; left: 0; right: 0; top: 200px; text-align: center;
    font-size: 41px; line-height: 53px; font-weight: 800; color: var(--blue); letter-spacing: -0.5px;
    -webkit-text-stroke: 1px #ffffff; paint-order: stroke fill; }
  .cover-title .accent { color: var(--orange); }

  .competence-title { top: 24px; }
  .chart-caption { position: absolute; left: 367px; top: 24px; font-size: 25px; font-weight: 700; color: var(--ink); letter-spacing: -0.3px; }

  .intro-text { position: absolute; left: 45px; top: 28px; font-size: 11.5px; line-height: 16px; font-weight: 700; color: var(--ink); text-transform: uppercase; }
</style>
</head>
<body>

<!-- Slide 1: cover -->
<section class="slide cover" style="top:86px;">
  <div class="cover-photo" role="img" aria-label="Photo of a business team meeting around a desk with a computer, charts and documents, seen from above"></div>
  <h1 class="cover-title">UNIFIED OPERATION CENTER<br>AND <span class="accent">AUGMENTED OPERATION</span><br>MANAGEMENT</h1>
</section>

<!-- Slide 2: people -->
<section class="slide people" style="top:718px;">
  <svg class="full" viewBox="0 0 986 555">
    <defs>
      <polygon id="penta" points="0,-78 74,-24 46,63 -46,63 -74,-24"/>
    </defs>
    <path d="M 320 455 A 181 181 0 1 1 670 455" fill="none" stroke="var(--orange)" stroke-width="4"/>
    <g fill="var(--blue)">
      <circle cx="313" cy="402" r="9"/><circle cx="322" cy="307" r="9"/><circle cx="382" cy="232" r="9"/>
      <circle cx="495" cy="192" r="9"/><circle cx="602" cy="232" r="9"/><circle cx="660" cy="307" r="9"/>
      <circle cx="671" cy="402" r="9"/>
    </g>
    <text x="491" y="338" text-anchor="middle" font-family="Poppins, sans-serif" font-size="42" font-weight="700" fill="var(--ink)">PEOPLE</text>

    <g font-family="Poppins, sans-serif" font-size="12" font-weight="700" fill="#fff" text-anchor="middle">
      <g transform="translate(495,90)"><use href="#penta" fill="var(--blue)"/>
        <path d="M0,-38 L22,-26 L22,0 L0,12 L-22,0 L-22,-26 Z M-22,-26 L0,-14 L22,-26 M0,-14 L0,12" fill="#fff" stroke="var(--blue)" stroke-width="2.5"/>
        <text y="38">AUGMENT</text></g>
      <g transform="translate(326,150) rotate(-12)"><use href="#penta" fill="var(--orange)"/>
        <g transform="rotate(12)"><circle cy="-18" r="20" fill="#fff"/><rect x="-3" y="-22" width="6" height="17" fill="var(--orange)"/><circle cy="-29" r="3.5" fill="var(--orange)"/>
        <text y="30">INFORM</text></g></g>
      <g transform="translate(659,150) rotate(12)"><use href="#penta" fill="var(--orange)"/>
        <g transform="rotate(-12)"><rect x="-22" y="-38" width="28" height="28" rx="3" fill="none" stroke="#fff" stroke-width="4"/><rect x="-10" y="-26" width="28" height="28" rx="3" fill="var(--orange)" stroke="#fff" stroke-width="4"/><path d="M-2,-18 L12,-8 L-2,2 Z" fill="#fff"/>
        <text y="30">UNIFY</text></g></g>
      <g transform="translate(237,268) rotate(-24)"><use href="#penta" fill="var(--blue)"/>
        <g transform="rotate(24)"><rect x="-17" y="-40" width="34" height="38" rx="6" fill="#fff"/><rect x="-12" y="-34" width="24" height="12" fill="var(--blue)"/><circle cx="-8" cy="-10" r="3" fill="var(--blue)"/><circle cx="8" cy="-10" r="3" fill="var(--blue)"/><path d="M-10,-2 L-15,6 M10,-2 L15,6" stroke="#fff" stroke-width="3"/>
        <text y="26">TRAIN</text></g></g>
      <g transform="translate(750,268) rotate(24)"><use href="#penta" fill="var(--blue)"/>
        <g transform="rotate(-24)"><circle cy="-38" r="6" fill="#fff"/><rect x="-8" y="-31" width="16" height="10" rx="4" fill="#fff"/><path d="M0,-20 L0,-12 M-16,-12 L16,-12 M-16,-12 L-16,-8 M16,-12 L16,-8" stroke="#fff" stroke-width="2.5" fill="none"/><circle cx="-16" cy="-3" r="6" fill="#fff"/><rect x="-24" y="4" width="16" height="10" rx="4" fill="#fff"/><circle cx="16" cy="-3" r="6" fill="#fff"/><rect x="8" y="4" width="16" height="10" rx="4" fill="#fff"/>
        <text y="32">COORDINATE</text></g></g>
      <g transform="translate(220,432) rotate(-36)"><use href="#penta" fill="var(--orange)"/>
        <g transform="rotate(36)"><circle cy="-22" r="20" fill="none" stroke="#fff" stroke-width="8" stroke-dasharray="7 5"/><circle cy="-22" r="13" fill="none" stroke="#fff" stroke-width="4"/><circle cy="-22" r="5" fill="#fff"/>
        <text y="28">SKILL</text></g></g>
      <g transform="translate(767,432) rotate(36)"><use href="#penta" fill="var(--orange)"/>
        <g transform="rotate(-36)"><circle cy="-24" r="17" fill="none" stroke="#fff" stroke-width="4"/><circle cy="-41" r="8" fill="#fff"/><circle cx="-15" cy="-14" r="8" fill="#fff"/><circle cx="15" cy="-14" r="8" fill="#fff"/>
        <text y="24">CONNECT</text></g></g>
    </g>
  </svg>
  <div class="footer-bar left"></div><div class="footer-bar right"></div>
  <span class="footer-label">UOC_AOM</span><span class="page-no">PAGE NO : 02</span>
</section>

<!-- Slide 3: competence chart -->
<section class="slide competence" style="top:1351px;">
  <div class="marker"></div>
  <h2 class="slide-title competence-title">COMPETENCE</h2>
  <p class="chart-caption">WORKFORCE TURNOVER MISSING EXPERIENCE</p>
  <svg class="full" viewBox="0 0 986 555">
    <g stroke="var(--grid)" stroke-width="1">
      <path d="M105 92V468M156 92V468M207 92V468M258 92V468M309 92V468M360 92V468M411 92V468M462 92V468M513 92V468M564 92V468M615 92V468M666 92V468M717 92V468M768 92V468M819 92V468M870 92V468M921 92V468"/>
      <path d="M54 132H943M54 183H943M54 234H943M54 285H943M54 336H943M54 387H943M54 438H943"/>
    </g>
    <path d="M54 90V468H943" fill="none" stroke="var(--ink)" stroke-width="2.5"/>
    <polyline points="54,468 232,300 273,300 451,134" fill="none" stroke="var(--orange)" stroke-width="2"/>
    <circle cx="451" cy="134" r="5" fill="var(--orange)"/>
    <polyline points="54,468 413,300 493,300 850,134" fill="none" stroke="var(--blue)" stroke-width="2"/>
    <circle cx="850" cy="134" r="5" fill="var(--blue)"/>
    <g font-family="Poppins, sans-serif" font-size="12" font-weight="700" fill="var(--blue)" text-anchor="middle">
      <text x="455" y="124">KNOWLEDGE</text><text x="856" y="124">EXPERIENCE</text>
    </g>
  </svg>
  <div class="footer-bar left"></div><div class="footer-bar right"></div>
  <span class="footer-label">UOC_AOM</span><span class="page-no">PAGE NO : 03</span>
</section>

<!-- Slide 4: AOM concept cycle -->
<section class="slide concept" style="top:1983px;">
  <div class="marker"></div>
  <p class="intro-text">Introduction to AOM (Augmented Operations Mangement) concept<br>Infos can help both people and the corporate in taking decisions.</p>
  <svg class="full" viewBox="0 0 986 555">
    <g fill="none" stroke="var(--ink)" stroke-width="2.2">
      <path d="M395 92 Q445 60 492 86"/><path d="M484 78 L493 87 L480 90"/>
      <path d="M656 254 Q685 290 650 330"/><path d="M662 325 L649 331 L648 318"/>
      <path d="M590 492 Q540 526 492 500"/><path d="M502 508 L491 499 L503 493"/>
      <path d="M284 350 Q260 310 292 270"/><path d="M279 276 L293 269 L296 282"/>
    </g>
    <circle cx="350" cy="196" r="100" fill="var(--blue)"/>
    <circle cx="549" cy="196" r="100" fill="var(--orange)"/>
    <circle cx="350" cy="394" r="100" fill="var(--orange)"/>
    <circle cx="549" cy="394" r="100" fill="var(--blue)"/>
    <g fill="none" stroke="#fff" stroke-width="5" stroke-linecap="round">
      <circle cx="350" cy="162" r="6" fill="#fff"/>
      <path d="M334 146 Q324 162 334 178M366 146 Q376 162 366 178M320 134 Q302 162 320 190M380 134 Q398 162 380 190"/>
    </g>
    <g fill="#fff">
      <rect x="530" y="128" width="38" height="62"/><rect x="518" y="150" width="12" height="40"/><rect x="568" y="150" width="12" height="40"/>
      <rect x="540" y="120" width="18" height="10"/>
      <g fill="var(--orange)"><rect x="536" y="138" width="6" height="8"/><rect x="546" y="138" width="6" height="8"/><rect x="556" y="138" width="6" height="8"/><rect x="536" y="154" width="6" height="8"/><rect x="556" y="154" width="6" height="8"/><rect x="544" y="174" width="10" height="16"/></g>
      <rect x="525" y="354" width="48" height="36" rx="5"/><rect x="538" y="345" width="22" height="12" rx="3" fill="none" stroke="#fff" stroke-width="4"/><rect x="525" y="368" width="48" height="3" fill="var(--blue)"/>
      <circle cx="350" cy="342" r="9"/><circle cx="332" cy="354" r="7"/><circle cx="368" cy="354" r="7"/>
      <path d="M322 368 L342 362 L358 362 L378 368 L372 390 L350 380 L328 390 Z"/>
    </g>
    <g font-family="Poppins, sans-serif" font-size="14" font-weight="700" fill="#fff" text-anchor="middle">
      <text x="350" y="226">2 MAIN STREAMS</text>
      <text x="549" y="226">AUGMENT</text><text x="549" y="244">CORPORATE</text><text x="549" y="262">VISIBILITY</text>
      <text x="350" y="426">AUGMENT PEOPLE</text>
      <text x="549" y="426">AUGMENTED</text><text x="549" y="444">OPERATIONS</text><text x="549" y="462">MANAGEMENT</text>
    </g>
  </svg>
  <div class="footer-bar left"></div><div class="footer-bar right"></div>
  <span class="footer-label">UOC_AOM</span><span class="page-no">PAGE NO : 04</span>
</section>

<!-- Slide 5: production performance -->
<section class="slide production" style="top:2615px;">
  <div class="marker"></div>
  <h2 class="slide-title">PRODUCTION PERFORMANCE</h2>
  <p class="slide-sub">Analysis of production, line and environment status to suggest best actions to keep production performance in target</p>
  <svg class="full" viewBox="0 0 986 555">
    <defs>
      <linearGradient id="photoA" x1="0" y1="0" x2="1" y2="1"><stop offset="0" stop-color="#b8b2a8"/><stop offset="1" stop-color="#2f3a55"/></linearGradient>
      <linearGradient id="photoB" x1="0" y1="0" x2="1" y2="1"><stop offset="0" stop-color="#4a4f52"/><stop offset="1" stop-color="#a89a86"/></linearGradient>
      <linearGradient id="photoC" x1="0" y1="0" x2="1" y2="1"><stop offset="0" stop-color="#d8d2c8"/><stop offset="1" stop-color="#2b2c30"/></linearGradient>
    </defs>
    <polygon points="89,139 365,139 331,473 48,473" fill="url(#photoA)" role="img" aria-label="Photo of two colleagues looking at a laptop in an office"/>
    <polygon points="373,139 646,139 605,473 334,473" fill="url(#photoB)" role="img" aria-label="Photo of a team working together at a meeting table"/>
    <polygon points="656,139 931,139 889,473 614,473" fill="url(#photoC)" role="img" aria-label="Photo of a smiling woman discussing with a colleague"/>
  </svg>
  <div class="footer-bar left"></div><div class="footer-bar right"></div>
  <span class="footer-label">UOC_AOM</span><span class="page-no">PAGE NO : 05</span>
</section>

<!-- Slide 6: internal logistic optimization -->
<section class="slide logistics" style="top:3246px;">
  <div class="marker"></div>
  <h2 class="slide-title">INTERNAL LOGISTIC OPTIMIZATION</h2>
  <p class="slide-sub">Analysis of production, line and environment status to optimize internal material movements<br>(raw material to the line, WMS missions, ...)</p>
  <svg class="full" viewBox="0 0 986 555">
    <defs>
      <linearGradient id="photoD" x1="0" y1="0" x2="1" y2="1"><stop offset="0" stop-color="#7a6a4c"/><stop offset="0.5" stop-color="#c9a878"/><stop offset="1" stop-color="#3a3f47"/></linearGradient>
    </defs>
    <rect x="48" y="142" width="883" height="340" fill="url(#photoD)" role="img" aria-label="Photo of a group of smiling colleagues walking together through a modern office"/>
  </svg>
  <div class="footer-bar left"></div><div class="footer-bar right"></div>
  <span class="footer-label">UOC_AOM</span><span class="page-no">PAGE NO : 06</span>
</section>

</body>
</html>
```